quickdeedsale.com redesign with wireframes, white space and custom form are very important

Need a new two column design that will convert easily to mobile responsive. Lots of white space. Winning design will probably be based on header area and making the custom form stand out. I want the header to be very much like www.tallgatevk.com except the form not to go up into the header.
Here are some of the websites I really like:
www.birchdwell.com
http://ourplotpurchasedirect.com/
http://kellbrightproperty.com/

We buy homes for cash and close fast. Our target is a home seller who is desperate to sell quickly.
I have uploaded my really ugly wireframe and my logo. I also uploaded my photo for the about us box and a possible photo to use for the header.
The copy on the wireframe is what I will be using except for the about us box.

Here is the exact link for video to frame in the top left box.
https://clipvault.example/Qm38pzrtLa

0592cd
85cae6
eaf1f7
fbee3d
ec1f27

• Everything on wireframe.
• Must use Verdana font and nothing should be smaller than 12 point. Most should be in 14 point. (except maybe inside of form)

```html
<!DOCTYPE html>
<html lang="en">
<head>
<meta charset="utf-8">
<title>quickdeedsale.com — Sell Your Home For Cash</title>
<link rel="stylesheet" href="https://fonts.googleapis.com/css2?family=Open+Sans:wght@400;600&family=Quicksand:wght@400;500&display=swap">
<style>
:root{
  --blue:#0592cd;
  --blue-dark:#0477a8;
  --sky:#85cae6;
  --ice:#eaf1f7;
  --ink:#333;
  --muted:#8a8f94;
  --rule:#d6dde3;
  --white:#fff;
  --night:#0b1f4a;
}
*{box-sizing:border-box;margin:0;padding:0}
html,body{width:1200px;height:3214px;overflow:hidden;background:var(--white)}
body{position:relative;font-family:"Quicksand",sans-serif;color:var(--ink)}
.abs{position:absolute}
.center{left:0;width:1200px;text-align:center}

/* header */
.hero{position:absolute;left:0;top:0;width:1200px;height:643px;
  background:linear-gradient(180deg,#0d1c44 0%,#1a3b7c 30%,#2f6fb4 55%,#1e9bd7 75%,#0f89c9 100%)}
.navbar{position:absolute;left:0;top:0;width:1200px;height:96px;background:rgba(5,146,205,.55)}
.brand{position:absolute;left:200px;top:30px;font:600 22px "Open Sans",sans-serif;color:var(--white);display:flex;align-items:center;gap:10px}
.brand-mark{width:18px;height:18px;background:var(--white)}
.nav{position:absolute;left:358px;top:58px;display:flex;gap:50px;font:400 17px "Open Sans",sans-serif;color:var(--white)}
.nav a{color:var(--white);text-decoration:none}
.topphone{position:absolute;left:862px;top:19px;font:400 19px "Open Sans",sans-serif;color:var(--white);display:flex;gap:8px;align-items:center}
.headline{top:228px;font:600 38px/40px "Open Sans",sans-serif;color:var(--white);letter-spacing:.5px;text-shadow:0 2px 4px #000}
.call{position:absolute;left:458px;top:359px;width:324px;height:56px;background:var(--blue);color:var(--white);
  font:400 26px/56px "Open Sans",sans-serif;text-align:center;box-shadow:0 3px 8px rgba(0,0,0,.35)}
.leadform{position:absolute;left:0;top:496px;width:1200px;height:147px;background:rgba(5,146,205,.55)}
.leadform h2{position:absolute;left:166px;top:20px;font:400 21px "Open Sans",sans-serif;color:var(--white)}
.field{position:absolute;height:34px;background:var(--ice);border:1px solid #c8d6e2;font:400 12px/32px "Open Sans",sans-serif;color:#555;padding-left:8px}
.submit{position:absolute;left:820px;top:104px;width:209px;height:36px;background:var(--blue);color:var(--white);font:600 17px/36px "Open Sans",sans-serif;text-align:center}

/* sections */
.avatar{position:absolute;left:569px;top:685px;width:62px;height:62px;border-radius:50%;background:radial-gradient(circle,#c9c3bd,#6f7780);border:3px solid var(--white);box-shadow:0 0 0 1px var(--rule)}
.title{font:400 38px "Open Sans",sans-serif;color:var(--blue)}
.lede{font:400 17px/25px "Quicksand",sans-serif;color:var(--muted)}
.rule{position:absolute;left:170px;width:860px;height:1px;background:var(--rule)}
.dots{position:absolute;left:0;width:1200px;display:flex;justify-content:center;gap:6px}
.dots i{width:9px;height:9px;border-radius:50%;border:1.5px solid var(--blue);background:var(--white)}
.dots i.on{background:var(--blue)}
.video{position:absolute;left:161px;top:1074px;width:466px;height:241px;background:#e9e8f7;border:1px solid #c9c7e6;display:flex;align-items:center;justify-content:center}
.ticks{position:absolute;left:685px;top:1124px;list-style:none;font:400 19px/47px "Quicksand",sans-serif;color:var(--muted)}
.ticks li,.reasons li{display:flex;align-items:center;gap:8px}
.sell h3{position:absolute;left:177px;top:1422px;width:430px;font:400 22px/30px "Open Sans",sans-serif;color:var(--blue)}
.sell p{position:absolute;left:177px;top:1510px;width:430px;font:400 17px/24px "Quicksand",sans-serif;color:var(--muted)}
.btn{position:absolute;background:var(--blue);color:var(--white);font:400 17px "Open Sans",sans-serif;display:flex;align-items:center;justify-content:center;box-shadow:3px 3px 0 #0a4f73}
.diamond{position:absolute;clip-path:polygon(50% 0,100% 50%,50% 100%,0 50%)}
.help{position:absolute;left:161px;top:1827px;width:450px;height:233px;background:linear-gradient(180deg,#0a1a3c,#1d4f87 55%,#0c2c55);color:var(--white);text-align:center}
.help strong{display:block;margin-top:82px;font:500 40px "Quicksand",sans-serif;letter-spacing:1px}
.help span{font:400 15px "Quicksand",sans-serif}
.reasons-h{position:absolute;left:643px;top:1828px;font:400 22px "Open Sans",sans-serif;color:var(--blue)}
.reasons{position:absolute;left:645px;top:1872px;list-style:none;font:400 18px/32.5px "Quicksand",sans-serif;color:var(--muted)}
.quote{top:2236px;font:400 18px/27px "Quicksand",sans-serif;color:var(--muted)}
.quote b{position:absolute;left:255px;top:-8px;font:400 60px "Open Sans",sans-serif;color:#999}
.who{top:2325px;font:400 18px/25px "Quicksand",sans-serif;color:#444}
.blogcard{position:absolute;left:150px;top:2532px;width:305px;height:241px;background:var(--ice)}
.blogcard h4{position:absolute;left:14px;top:16px;font:600 17px "Open Sans",sans-serif;color:#222}
.blogcard h4 em{font-style:normal;font-weight:400;color:var(--blue)}
.blogcard .bar{position:absolute;left:14px;top:46px;width:276px;height:1px;background:#bbb}
.blogcard p{position:absolute;left:14px;top:60px;width:280px;font:400 12.5px/18px "Open Sans",sans-serif;color:#666}
.more{font:400 12.5px "Open Sans",sans-serif;color:#444}
.more::after{content:" →";color:var(--blue);font-weight:600}
.caption{position:absolute;top:2774px;width:305px;font:400 12.5px/17px "Open Sans",sans-serif;color:#333}
.footer{position:absolute;left:0;top:2896px;width:665px;height:297px;background:var(--blue);color:var(--white)}
.footer h5{position:absolute;left:549px;top:26px;font:400 22px "Open Sans",sans-serif}
.foot-brand{position:absolute;left:108px;top:125px;font:600 24px "Open Sans",sans-serif;color:var(--ice)}
.contact{position:absolute;left:365px;list-style:none;font:400 17px/23px "Open Sans",sans-serif}
.contact li{position:absolute;left:0;width:290px;display:flex;gap:12px}
.map{position:absolute;left:665px;top:2896px;width:535px;height:297px;background:linear-gradient(135deg,#eee8dc,#e2ddd2 50%,#d7dfe6)}
.copy{top:3186px;font:400 12px "Open Sans",sans-serif;color:#888}
</style>
</head>
<body>

<header class="hero" role="img" aria-label="Modern luxury house with glowing pool at dusk"></header>
<nav class="navbar">
  <div class="brand"><span class="brand-mark"></span>quickdeedsale.com</div>
  <div class="nav"><a>Sell Your Home</a><a>How it works</a><a>Stop foreclosure</a><a>Probate</a><a>Contact</a></div>
  <div class="topphone">
    <svg width="18" height="18" viewBox="0 0 24 24"><path fill="#fff" d="M6.6 10.8a15 15 0 0 0 6.6 6.6l2.2-2.2c.3-.3.7-.4 1-.2 1.1.4 2.3.6 3.6.6.6 0 1 .4 1 1V20c0 .6-.4 1-1 1A17 17 0 0 1 3 4c0-.6.4-1 1-1h3.5c.6 0 1 .4 1 1 0 1.3.2 2.5.6 3.6.1.3 0 .7-.2 1z"/></svg>
    407-555-0186
  </div>
</nav>
<h1 class="abs center headline">SELL YOUR HOME FOR CASH IN 8 DAYS<br>WE BUY HOUSES NATIONWIDE.</h1>
<div class="call">CALL NOW</div>

<form class="leadform">
  <h2>Yes, I want to sell my home fast!</h2>
  <div class="field" style="left:166px;top:64px;width:214px">Your Name</div>
  <div class="field" style="left:388px;top:64px;width:207px">Your phone number</div>
  <div class="field" style="left:603px;top:64px;width:209px">Your Email Address</div>
  <div class="field" style="left:820px;top:64px;width:209px">Property Address</div>
  <div class="field" style="left:166px;top:104px;width:214px">Repairs needed if any</div>
  <div class="field" style="left:388px;top:104px;width:207px">Asking price</div>
  <div class="field" style="left:603px;top:104px;width:209px">Comments</div>
  <div class="submit">SUBMIT</div>
</form>

<section class="about">
  <div class="avatar" role="img" aria-label="Portrait photo of the owner"></div>
  <h2 class="abs center title" style="top:765px">ABOUT US</h2>
  <p class="abs center lede" style="top:830px">Owned and operated in Orlando Florida since 2001. Oldest Continuous<br>operated website in country.</p>
  <div class="rule" style="top:916px"></div>
  <div class="dots" style="top:912px"><i class="on"></i></div>
</section>

<section class="what">
  <h2 class="abs center title" style="top:952px">WHAT WE DO</h2>
  <p class="abs center lede" style="top:1017px">These are the benefits of selling your home to us.</p>
  <div class="video" role="img" aria-label="Embedded video player">
    <svg width="68" height="68" viewBox="0 0 68 68"><circle cx="34" cy="34" r="30" fill="none" stroke="#9a9aa8" stroke-width="5"/><circle cx="34" cy="34" r="20" fill="#9a9aa8"/><path d="M29 24l13 10-13 10z" fill="#e9e8f7"/></svg>
  </div>
  <ul class="ticks">
    <li><svg width="18" height="14" viewBox="0 0 18 14"><path d="M1 7l5 5L17 1" fill="none" stroke="#85cae6" stroke-width="2"/></svg>You pick the closing date</li>
    <li><svg width="18" height="14" viewBox="0 0 18 14"><path d="M1 7l5 5L17 1" fill="none" stroke="#85cae6" stroke-width="2"/></svg>You pay NO commissions or fees</li>
    <li><svg width="18" height="14" viewBox="0 0 18 14"><path d="M1 7l5 5L17 1" fill="none" stroke="#85cae6" stroke-width="2"/></svg>You don't have to paint, clean or make repairs</li>
  </ul>
  <div class="rule" style="top:1385px"></div>
  <div class="dots" style="top:1381px"><i></i><i class="on"></i></div>
</section>

<section class="sell">
  <h3>Sell your home or house fast for cash to a professional investor company. We buy Houses and close quickly.</h3>
  <p>Selling a home on your own has never been easier. From Orlando to Greensboro - and all points in between- you can sell your home today without any hassles. Call 1-800-555-0142 or fill out the form below to get a written offer on your home in just 36 hours. Sell today online to people that care</p>
  <div class="btn" style="left:177px;top:1701px;width:166px;height:40px">READ MORE</div>
  <div class="diamond" style="left:643px;top:1406px;width:262px;height:262px;background:linear-gradient(135deg,#cdd6e3,#e8d8a8 55%,#7f8f64)" role="img" aria-label="Photo of a yellow two-storey house"></div>
  <div class="diamond" style="left:797px;top:1440px;width:234px;height:234px;background:linear-gradient(135deg,#2d5fb0,#5c86c8 50%,#2a3d6a)" role="img" aria-label="Photo of a modern house at night"></div>
  <div class="diamond" style="left:715px;top:1570px;width:220px;height:220px;background:linear-gradient(135deg,#3b6cc0,#8fa9d6 50%,#3c4a66)" role="img" aria-label="Photo of a lit modern home"></div>
</section>

<section class="reasons-block">
  <div class="help" role="img" aria-label="Modern home lit at night"><strong>We Can Help.</strong><span>We Are The Best House Buyer Around</span></div>
  <h3 class="reasons-h">If you need to sell a home fast because of</h3>
  <ul class="reasons">
    <li><svg width="16" height="12" viewBox="0 0 18 14"><path d="M1 7l5 5L17 1" fill="none" stroke="#85cae6" stroke-width="2"/></svg>Divorce or Bankruptcy</li>
    <li><svg width="16" height="12" viewBox="0 0 18 14"><path d="M1 7l5 5L17 1" fill="none" stroke="#85cae6" stroke-width="2"/></svg>Foreclosure</li>
    <li><svg width="16" height="12" viewBox="0 0 18 14"><path d="M1 7l5 5L17 1" fill="none" stroke="#85cae6" stroke-width="2"/></svg>Landlord problems - evictions with tenants</li>
    <li><svg width="16" height="12" viewBox="0 0 18 14"><path d="M1 7l5 5L17 1" fill="none" stroke="#85cae6" stroke-width="2"/></svg>Inherited property in probate</li>
    <li><svg width="16" height="12" viewBox="0 0 18 14"><path d="M1 7l5 5L17 1" fill="none" stroke="#85cae6" stroke-width="2"/></svg>Termites, mold, flood or fire damage.</li>
    <li><svg width="16" height="12" viewBox="0 0 18 14"><path d="M1 7l5 5L17 1" fill="none" stroke="#85cae6" stroke-width="2"/></svg>Moving or can't afford mortgage payments</li>
  </ul>
  <div class="rule" style="top:2124px"></div>
  <div class="dots" style="top:2120px"><i></i><i></i><i class="on"></i></div>
</section>

<section class="testimonials">
  <h2 class="abs center title" style="top:2161px">SELLER TESTIMONIALS</h2>
  <svg class="abs" style="left:142px;top:2240px" width="26" height="52" viewBox="0 0 26 52"><path d="M24 2L3 26l21 24" fill="none" stroke="#0592cd" stroke-width="4"/></svg>
  <svg class="abs" style="left:1022px;top:2240px" width="26" height="52" viewBox="0 0 26 52"><path d="M2 2l21 24L2 50" fill="none" stroke="#0592cd" stroke-width="4"/></svg>
  <div class="abs center quote"><b>“</b>I just wanted to thank you for buying my home in Winter Park. You made it<br>fast and easy and kept me well informed the whole way.</div>
  <div class="abs center who">Dorian Maleck<br>Winter Park</div>
  <div class="rule" style="top:2449px"></div>
  <div class="dots" style="top:2445px"><i></i><i></i><i></i><i class="on"></i></div>
</section>

<section class="blog">
  <div class="blogcard">
    <h4>LATEST <em>BLOG</em></h4>
    <div class="bar"></div>
    <p>Plot Purchase Direct is known for its famous makeovers of old houses, now Plot Purchase Direct has done a different type of makeover – its website! Through its updated website, you now have clearer communication and quicker access ...</p>
    <span class="more abs" style="left:14px;top:210px">READ MORE</span>
  </div>
  <div class="abs" style="left:457px;top:2532px;width:304px;height:241px;background:linear-gradient(180deg,#d6e3ee,#c7a983 45%,#7b8a5a)" role="img" aria-label="Photo of a craftsman style house"></div>
  <div class="abs" style="left:766px;top:2532px;width:303px;height:241px;background:linear-gradient(180deg,#e4e4e4,#5d5d5d 45%,#8a8a80)" role="img" aria-label="Black and white photo of a brick house"></div>
  <p class="caption" style="left:457px">Some of the cities where we buy houses. Not all are listed.</p>
  <p class="caption" style="left:766px">We buy nice pretty houses and some ugly ones as well.</p>
  <span class="more abs" style="left:668px;top:2827px">READ MORE</span>
  <span class="more abs" style="left:975px;top:2827px">READ MORE</span>
</section>

<footer class="footer">
  <h5>CONTACT</h5>
  <div class="foot-brand">quickdeedsale.com</div>
  <ul class="contact">
    <li style="top:80px"><svg width="28" height="28" viewBox="0 0 24 24"><path fill="#fff" d="M12 2a7 7 0 0 0-7 7c0 5 7 13 7 13s7-8 7-13a7 7 0 0 0-7-7zm0 9.5A2.5 2.5 0 1 1 12 6.5a2.5 2.5 0 0 1 0 5z"/></svg>4820 Tamsin Ave #310 Winter<br>Park, FL 32789</li>
    <li style="top:146px"><svg width="28" height="28" viewBox="0 0 24 24"><rect x="2" y="2" width="20" height="20" rx="4" fill="#fff"/><path fill="#0592cd" d="M8.2 10.4a9 9 0 0 0 4 4l1.3-1.3c.2-.2.4-.2.6-.1.7.2 1.4.4 2.1.4.3 0 .6.2.6.6V16c0 .3-.3.6-.6.6A10 10 0 0 1 6.3 6.7c0-.3.3-.6.6-.6h2c.4 0 .6.3.6.6 0 .7.1 1.5.4 2.1 0 .2 0 .5-.1.6z"/></svg>407-555-0186</li>
    <li style="top:200px"><svg width="28" height="28" viewBox="0 0 24 24"><rect x="2" y="2" width="20" height="20" rx="4" fill="#fff"/><rect x="6" y="8" width="12" height="8" fill="none" stroke="#0592cd" stroke-width="1.5"/><path d="M6 8l6 5 6-5" fill="none" stroke="#0592cd" stroke-width="1.5"/></svg>deals@quickdeedsale.com</li>
  </ul>
</footer>
<div class="map" role="img" aria-label="Street map with location pin">
  <svg class="abs" style="left:252px;top:110px" width="36" height="48" viewBox="0 0 24 32"><path fill="#5a8ee0" d="M12 0a11 11 0 0 0-11 11c0 8 11 21 11 21s11-13 11-21A11 11 0 0 0 12 0z"/><circle cx="12" cy="11" r="4" fill="#fff"/></svg>
</div>
<p class="abs center copy">©2015 copyright quickdeedsale.com</p>

</body>
</html>
```